Stationery Design Project

Hi All,

We need you to design stationary for a new Business and Accounting Advisory Firm. We have already got the logo designed and it is attached. If you could also if possible, match the fonts in your design to that on the logo’s provided.

What we need:
- Business Card
- A4 Letter head
- A4 Folders
- PPT template (Title page and regular page)

And what ever else you want to throw in.

We are in the process of getting the web site designed, however below is a list of websites which we like which will give you an understanding of the style that we are going for.

- plivant.example
- moldrabay.example
- tarvenhook.example
- quillorbank.example

I look forward to your seeing your design.
Updates

Hi All,

I have just realised that I forgot that i need to include a Sworn Ledgerkeepers image on the letter head, please find attaced as File 1. Could you please have this image in the bottom left header.

Regards,

Marcus

Industry/Entity Type

Business

Requirements
Must have
• Outputs:
- Documents ready to print
- Generic editable information
- Pdf copies of the documents
- Word version of letterhead

```html
<!DOCTYPE html>
<html lang="en">
<head>
<meta charset="utf-8">
<title>Harrowmere Partners – Business Cards</title>
<link rel="stylesheet" href="https://fonts.googleapis.com/css2?family=EB+Garamond:wght@400;500&family=Tinos:wght@400;700&display=swap">
<style>
  :root {
    --backdrop: #898c8f;
    --paper: #ffffff;
    --brand-blue: #3a5a9c;
    --brand-blue-deep: #2f4f94;
    --brand-cyan: #3fb5d6;
    --brand-orange: #f6a623;
    --brand-orange-deep: #f07f1e;
    --ink: #333333;
    --ink-dark: #111111;
    --rule: #b5b5b5;
  }
  * { margin: 0; padding: 0; box-sizing: border-box; }
  html, body { width: 1200px; height: 709px; overflow: hidden; }
  body {
    background: var(--backdrop);
    position: relative;
    font-family: "Tinos", "Times New Roman", serif;
  }
  .card {
    position: absolute;
    width: 558px;
    height: 319px;
    background: var(--paper);
    border: 1px solid #6f7275;
    overflow: hidden;
  }
  .card--front { left: 322px; top: 21px; }
  .card--back { left: 25px; top: 364px; border: none;
    background: radial-gradient(circle at 50% 46%, var(--brand-cyan) 0%, #3a7fbd 28%, var(--brand-blue-deep) 62%, #33569a 100%); }
  .card--plain { left: 618px; top: 364px; }

  .brand {
    position: absolute;
    display: flex;
    align-items: center;
    gap: 12px;
  }
  .brand__mark {
    width: 34px; height: 34px;
    background: var(--brand-orange);
    flex: none;
  }
  .brand__name {
    font-family: "EB Garamond", Georgia, serif;
    font-weight: 400;
    font-size: 33px;
    color: var(--brand-blue);
    white-space: nowrap;
  }
  .card--front .brand { left: 108px; top: 55px; }
  .card--plain .brand { left: 0; right: 0; top: 140px; justify-content: center; }
  .card--plain .brand__name { font-size: 36px; }

  .holder {
    position: absolute;
    right: 302px;
    top: 164px;
    text-align: right;
    color: var(--ink);
    font-size: 16px;
    line-height: 21px;
  }
  .holder__name { font-weight: 700; font-size: 21px; color: var(--brand-blue); line-height: 24px; }
  .holder__role { margin-bottom: 10px; }

  .divider {
    position: absolute;
    left: 273px; top: 158px;
    width: 1px; height: 107px;
    background: var(--rule);
  }

  .contacts {
    position: absolute;
    left: 287px; top: 166px;
    list-style: none;
    font-size: 17px;
    line-height: 23.5px;
    color: var(--ink);
  }
  .contacts li { display: flex; align-items: center; gap: 5px; }
  .contacts svg { width: 11px; height: 11px; fill: var(--brand-blue); flex: none; }
  .contacts__web { color: var(--ink-dark); }

  .accent-band {
    position: absolute;
    left: 0; bottom: 0;
    width: 100%; height: 17px;
  }

  .back__name {
    position: absolute;
    left: 0; right: 0; top: 112px;
    text-align: center;
    font-family: "EB Garamond", Georgia, serif;
    font-size: 52px;
    color: var(--paper);
  }
  .web-line {
    position: absolute;
    left: 0; right: 0;
    text-align: center;
    letter-spacing: 1.5px;
    font-size: 18px;
  }
  .card--back .web-line { top: 267px; color: var(--paper); }
  .card--plain .web-line { top: 242px; color: var(--ink-dark); }
</style>
</head>
<body>

<section class="card card--front" aria-label="Business card front">
  <div class="brand">
    <span class="brand__mark"></span>
    <span class="brand__name">Harrowmere Partners</span>
  </div>

  <div class="holder">
    <p class="holder__name">Your Name</p>
    <p class="holder__role">Designation</p>
    <p>Street Name, City Name</p>
    <p>State, City Zip Code</p>
  </div>

  <div class="divider"></div>

  <ul class="contacts">
    <li><svg viewBox="0 0 12 12"><path d="M6 0a6 6 0 1 0 0 12A6 6 0 0 0 6 0zm0 1.3a4.7 4.7 0 1 1 0 9.4 4.7 4.7 0 0 1 0-9.4zM4 3l1.3 0 .5 1.5-.8.7c.4.9 1 1.5 1.8 1.9l.7-.8 1.5.5V8c-3 .3-5.3-2-5-5z"/></svg>0123-456-789</li>
    <li><svg viewBox="0 0 12 12"><path d="M2.5 2h7l1.5 4v4H9.5V9h-7v1H1V6zm.8 1.3L2.5 5.5h7l-.8-2.2zM3 6.5a.8.8 0 1 0 0 1.6.8.8 0 0 0 0-1.6zm6 0a.8.8 0 1 0 0 1.6.8.8 0 0 0 0-1.6z"/></svg>0123-456-789</li>
    <li><svg viewBox="0 0 12 12"><path d="M1 3h10v7H1zm1 1v.4l4 2.6 4-2.6V4z"/></svg>info@harrowmerepartners.example</li>
    <li class="contacts__web"><svg viewBox="0 0 12 12"><path d="M6 0a6 6 0 1 0 0 12A6 6 0 0 0 6 0zm-.6 1.5v2H3.2a4.6 4.6 0 0 1 2.2-2zm1.2 0a4.6 4.6 0 0 1 2.2 2H6.6zM1.6 4.7h3.8v2.6H1.6a4.6 4.6 0 0 1 0-2.6zm5 0h3.8a4.6 4.6 0 0 1 0 2.6H6.6zM3.2 8.5h2.2v2a4.6 4.6 0 0 1-2.2-2zm3.4 0h2.2a4.6 4.6 0 0 1-2.2 2z"/></svg>www.harrowmerepartners.example</li>
  </ul>

  <svg class="accent-band" viewBox="0 0 558 17" preserveAspectRatio="none" aria-hidden="true">
    <defs>
      <linearGradient id="band-blue" x1="0" x2="1" y1="0" y2="0">
        <stop offset="0" stop-color="#2f4f94"/>
        <stop offset="1" stop-color="#3fb5d6"/>
      </linearGradient>
      <linearGradient id="band-orange" x1="0" x2="1" y1="0" y2="0">
        <stop offset="0" stop-color="#fcc233"/>
        <stop offset="1" stop-color="#f07f1e"/>
      </linearGradient>
    </defs>
    <polygon points="0,0 278,0 262,17 0,17" fill="url(#band-blue)"/>
    <polygon points="288,0 558,0 558,17 272,17" fill="url(#band-orange)"/>
  </svg>
</section>

<section class="card card--back" aria-label="Business card back">
  <p class="back__name">Harrowmere Partners</p>
  <p class="web-line">www.harrowmerepartners.example</p>
</section>

<section class="card card--plain" aria-label="Business card alternate back">
  <div class="brand">
    <span class="brand__mark"></span>
    <span class="brand__name">Harrowmere Partners</span>
  </div>
  <p class="web-line">www.harrowmerepartners.example</p>
</section>

</body>
</html>
```